Under Morning Lantern website

I need a website to sell my t-shirt designs. I have around 5 designs I plan to sell on my initial launch, but only 3 photos at the moment. I would love a main page with the product images below maybe a large nicely designed header image, showing products with their sizes, item name/description, a way to add to cart and a review system like stars below each product image. Maybe a share option to Snapwell, Friendbook, Chirper, Pinterest, etc. would be cool too. Also on the main page under the product images a section showcasing my Snapwell photos for the company. Then a section where I will include an About Me video from like Viewtube. Lastly, on the main page an option to join my Mailing List at the footer with links to my Friendbook and Snapwell social accounts, links to pages (About Me, Shop, Snapwell page, & Contact Us) as well as Track Order.

The other 4 pages will be for an About Me, which is the video I will make later that will be from Viewtube. Then the Shop page. Then the Snapwell page showcasing all the photos I plan to use to market the products, and a Contact Us Page.

I plan to possibly connect this to Shopify, so showcasing payment options (Palo, Birch Pay, Wayfarer, etc.) would be nice.

Lastly, I don't plan on doing returns/exchanges so maybe an area showing that would be nice too. ALL SALES FINAL

Mobile Friendly!

1st image is logo and other 4 images are t-shirt designs

Coded - Design and coding required

5+ page

• Separate pages, No Refunds (All Sales Final), Add to Cart, Way to Purchase

```html
<!DOCTYPE html>
<html lang="en">
<head>
<meta charset="utf-8">
<title>Under Morning Lantern – Contact Us</title>
<link href="https://fonts.googleapis.com/css2?family=Poppins:wght@400;500;600&family=Roboto:wght@400;500;700;900&display=swap" rel="stylesheet">
<style>
:root{
  --brand:#03a9ec;
  --ink:#222;
  --muted:#777;
  --line:#cfcfcf;
  --footer:#2b2b2b;
  --footer-deep:#222;
  --footer-text:#bbb;
  --white:#fff;
}
*{box-sizing:border-box;margin:0;padding:0}
html,body{width:913px;height:1200px;overflow:hidden;background:var(--white)}
body{position:relative;font-family:'Poppins',sans-serif;color:var(--ink)}
.abs{position:absolute}
/* header */
.hero{left:0;top:0;width:913px;height:238px;background:var(--brand)}
.brand{left:90px;top:30px;color:#111;font-family:'Roboto',sans-serif;font-weight:900;line-height:1}
.brand .mark{font-size:34px;letter-spacing:1px;display:block}
.brand .tag{font-size:6.5px;letter-spacing:2px;display:block;margin-top:3px;padding-left:10px;color:#111}
.nav{left:270px;top:33px;width:483px;height:34px;background:var(--white);border-radius:17px;overflow:hidden;display:flex;align-items:center;font-family:'Roboto',sans-serif;font-size:13px}
.nav a{color:#333;text-decoration:none;margin-left:34px;position:relative}
.nav a:first-child{margin-left:35px}
.nav a.active{color:var(--brand)}
.nav a.active::after{content:"";position:absolute;left:50%;bottom:-7px;width:3px;height:3px;margin-left:-1.5px;border-radius:50%;background:var(--brand)}
.nav .track{position:absolute;right:0;top:0;width:130px;height:34px;background:#000;color:var(--white);display:flex;align-items:center;justify-content:center;margin:0;border-radius:0 17px 17px 0}
.cart{left:798px;top:40px}
.cart .count{position:absolute;left:13px;top:-5px;width:12px;height:12px;border-radius:50%;background:#000;color:var(--white);font:500 7px/12px 'Roboto',sans-serif;text-align:center}
.page-title{left:0;top:148px;width:913px;text-align:center;color:var(--white);font:700 26px 'Roboto',sans-serif}
.crumbs{left:0;top:188px;width:913px;text-align:center;color:var(--white);font:400 12px 'Roboto',sans-serif;word-spacing:2px}
.crumbs span{margin:0 12px}
/* contact */
.hello{left:120px;top:285px;font-size:23px;line-height:35px}
.hello .lead{color:var(--brand)}
.socials{left:120px;top:402px;display:flex;gap:18px;font-size:9px;color:#333}
.field{left:466px;width:333px;height:29px;border:1px solid var(--line);font-size:10px;color:#888;padding:8px 13px}
.send{left:468px;top:507px;width:97px;height:32px;background:var(--brand);color:var(--white);font-size:10.5px;text-align:center;line-height:32px}
/* gallery */
.gallery-title{left:197px;top:592px;font-size:22px;font-weight:600;color:#333}
.gallery-text{left:197px;top:627px;width:520px;font-size:12px;line-height:16px;color:#333}
/* footer */
.footer{left:0;top:978px;width:913px;height:164px;background:var(--footer)}
.bottom{left:0;top:1142px;width:913px;height:58px;background:var(--footer-deep)}
.f-policy{left:90px;top:1012px;color:var(--brand);font-family:'Roboto',sans-serif;font-size:9.5px;line-height:20px}
.f-rule{left:88px;top:1059px;width:147px;height:1px;background:#444}
.f-contact{left:90px;top:1072px;color:var(--footer-text);font-family:'Roboto',sans-serif;font-size:10px;line-height:19px}
.vline{width:1px;background:#3c3c3c}
.f-heading{color:var(--white);font-family:'Roboto',sans-serif;font-size:12px}
.f-links{left:282px;top:1040px;color:var(--footer-text);font-family:'Roboto',sans-serif;font-size:10.5px;line-height:17.5px}
.f-note{left:397px;top:1030px;color:var(--footer-text);font-family:'Roboto',sans-serif;font-size:10.5px}
.sub{left:390px;top:1060px;width:277px;height:29px;border-radius:15px;overflow:hidden;display:flex;font-family:'Roboto',sans-serif;font-size:10.5px}
.sub .input{flex:1;background:#eef2f6;color:#888;padding:8px 20px}
.sub .btn{width:90px;background:var(--brand);color:var(--white);font-weight:700;text-align:center;line-height:29px}
.f-social{left:397px;top:1102px;display:flex;gap:10px;color:#999;font-family:'Roboto',sans-serif;font-size:8px}
.f-brand{left:722px;top:1008px;color:var(--brand);font-family:'Roboto',sans-serif;font-weight:900;line-height:1}
.f-brand .mark{font-size:25px;display:block}
.f-brand .tag{font-size:4.8px;letter-spacing:1.5px;display:block;margin-top:3px;padding-left:8px}
.f-track{left:725px;top:1060px;width:102px;height:29px;background:var(--brand);color:var(--white);font-family:'Roboto',sans-serif;font-size:10.5px;text-align:center;line-height:29px}
.copy{left:91px;top:1163px;color:#999;font-size:10.5px}
.cards{left:561px;top:1159px;display:flex;gap:7px}
.cards div{width:38px;height:23px;background:var(--white);border-radius:3px;font-family:'Roboto',sans-serif;font-size:6.5px;font-weight:700;color:#333;text-align:center;line-height:23px}
</style>
</head>
<body>
<div class="abs hero"></div>
<div class="abs brand"><span class="mark">U.M.L.</span><span class="tag">UNDER MORNING LANTERN</span></div>
<nav class="abs nav">
  <a href="#">About</a><a href="#">Shop</a><a href="#">Snapwell</a><a href="#" class="active">Contact</a>
  <a href="#" class="track">Track Order</a>
</nav>
<div class="abs cart">
  <svg width="18" height="17" viewBox="0 0 18 17" fill="none" stroke="#fff" stroke-width="1.3"><path d="M1 2h3l2 9h9l2-7H5"/><circle cx="7.5" cy="14.5" r="1.3"/><circle cx="14" cy="14.5" r="1.3"/></svg>
  <div class="count">0</div>
</div>
<h1 class="abs page-title">CONTACT US</h1>
<div class="abs crumbs">Home<span>|</span>Contact Us</div>

<div class="abs hello"><div class="lead">Don’t be sastranger</div><div>just say hello.</div></div>
<div class="abs socials"><span>Friendbook</span><span>Chirper</span><span>Snapwell</span><span>Linkly</span></div>

<div class="abs field" style="top:292px">Name</div>
<div class="abs field" style="top:333px">E-mail</div>
<div class="abs field" style="top:375px;height:117px">Message</div>
<div class="abs send">Send Us</div>

<h2 class="abs gallery-title">Snapwell</h2>
<p class="abs gallery-text">Meet your fellow Humans! Show us your UML style on Chirper, Snapwell or Friendbook and tag @UML for a chance to win free tees and be featured on our site!</p>
<div class="abs" role="img" aria-label="Purple t-shirt product shot on dark background" style="left:194px;top:682px;width:242px;height:224px;background:radial-gradient(circle at 50% 50%,#6f5a9c 0 32%,#383f4b 33%)"></div>
<div class="abs" role="img" aria-label="Customer photo outdoors on rocks" style="left:445px;top:682px;width:136px;height:108px;background:linear-gradient(160deg,#5b98c4,#8a8a86 60%,#6a6762)"></div>
<div class="abs" role="img" aria-label="Person in black hoodie in a field" style="left:589px;top:682px;width:130px;height:108px;background:linear-gradient(180deg,#e8e8e6,#9a8c72 60%,#4a4034)"></div>
<div class="abs" role="img" aria-label="Person in white tee against stone wall" style="left:445px;top:798px;width:136px;height:108px;background:linear-gradient(135deg,#5a5f63,#7d8286 60%,#4d5256)"></div>
<div class="abs" role="img" aria-label="Person in hoodie sitting on a boardwalk" style="left:589px;top:798px;width:130px;height:108px;background:linear-gradient(180deg,#b9cad3,#8ea3ae 55%,#a6a29d)"></div>

<footer>
<div class="abs footer"></div>
<div class="abs bottom"></div>
<div class="abs f-policy">ALL SALES FINAL. NO REFUNDS,<br>RETURNS OR EXCHANGES</div>
<div class="abs f-rule"></div>
<div class="abs f-contact">+xxx xxxx xxxxx<br>xxxxxxx@mailbox.com</div>
<div class="abs vline" style="left:247px;top:1014px;height:108px"></div>
<div class="abs f-heading" style="left:282px;top:1012px">Contact Us</div>
<div class="abs f-links">Home<br>About<br>Services<br>Contact</div>
<div class="abs vline" style="left:363px;top:1014px;height:108px"></div>
<div class="abs f-heading" style="left:397px;top:1010px">Email Newsletter</div>
<div class="abs f-note">Sale upto 20 % off for your next purchase inthis month!</div>
<div class="abs sub"><div class="input">Email address</div><div class="btn">Subscribe</div></div>
<div class="abs f-social"><span>Chirper</span><span>Sharely</span><span>Friendbook</span><span>Viewtube</span><span>Snapwell</span></div>
<div class="abs vline" style="left:688px;top:1014px;height:108px"></div>
<div class="abs f-brand"><span class="mark">U.M.L.</span><span class="tag">UNDER MORNING LANTERN</span></div>
<div class="abs f-track">Track Order</div>
<div class="abs copy">© 2020 UML Under Morning Lantern &nbsp;| All Rights Reserved</div>
<div class="abs cards"><div>Palo</div><div>Orbita</div><div>Kestrel</div><div>Pennyway</div><div>Dunmore</div><div>Wayfarer</div></div>
</footer>
</body>
</html>
```